Brightway Haus Inc. Business Card Design

Brightway Haus Inc. is in search of a great clean design for our business cards!

Looking to incorporate our full logo and watermark on side one (however, I am open to having the text and watermark separated within the design.)

On side two, I am looking to have contact information (Name, Position, Phone #, Email, Website (www.thebrightwayhaus.ca). Can have the logo and/or watermark as part of the design if applicable.

Please add tagline "Where Shine Counts" on either side 1 or 2. This tagline can be in a sans serif, serif or cursive font as long as it compliments overall design. Capitalization can be title or sentence case depending on how it fits within the design.

Get creative!! Looking for a clean, crisp, premium design! Looking for a glossy card finish with spot UV features when printed. Cards will also be printed with rounded corners. Standard dimensions (3.5 x 2).

Target Market(s)

B2B - primary clients are business owners or property management corporations. (residential jobs are few and far between)

Industry/Entity Type

Business

Contact Information for Business Card

- clean, crisp design
- double sided
- spot UV accents and glossy finish upon printing
- standard business card size (3.5 x 2) with rounded corners
- please see project description for requirements per side

Font styles to use
Sans Serif

Requirements
Must have
• - adequate bleeds with print ready files
• - cohesive design elements between side 1 & 2
• - spot UV elements (can be on both sides or just one, use your discretion)
• - colour pallet should match the logo file provided
• - incorporate tagline "where shine counts" (this tagline can be in a serif or sans serif font as long as it is complimentary to the overall design.
Nice to have
• - Premium elements with a clean design
Should not have
• - Please omit cartoon or whimsical like designs, think premium.
• - Colours should not stray from the pallet of the provided logo.

```html
<!DOCTYPE html>
<html lang="en">
<head>
<meta charset="utf-8">
<title>Brightway Haus Inc. Business Card</title>
<link href="https://fonts.googleapis.com/css2?family=Work+Sans:wght@400;500;700&display=swap" rel="stylesheet">
<style>
  :root {
    --stage: #2b2b2d;
    --navy: #1b2658;
    --teal: #17b8bd;
    --white: #ffffff;
    --paper: #ffffff;
  }
  * { margin: 0; padding: 0; box-sizing: border-box; }
  html, body { width: 1200px; height: 900px; overflow: hidden; }
  body {
    background: var(--stage);
    font-family: "Work Sans", sans-serif;
    position: relative;
  }
  .card {
    position: absolute;
    left: 250px;
    width: 700px;
    height: 400px;
    border-radius: 18px;
    overflow: hidden;
  }
  .card-front { top: 40px; background: var(--navy); }
  .card-back { top: 470px; background: var(--paper); }

  .brand {
    position: absolute;
    display: flex;
    align-items: center;
    gap: 14px;
    font-weight: 700;
    letter-spacing: -0.5px;
  }
  .brand-square { display: block; background: var(--teal); }
  .card-front .brand {
    left: 50%; top: 150px; transform: translateX(-50%);
    color: var(--white); font-size: 46px; white-space: nowrap;
  }
  .card-front .brand-square { width: 44px; height: 44px; }
  .tagline {
    position: absolute; left: 0; right: 0; bottom: 56px;
    text-align: center; color: var(--white);
    font-size: 17px; font-weight: 500; letter-spacing: 5px;
    text-transform: uppercase;
  }

  .card-back .brand {
    right: 40px; top: 58px; color: var(--teal); font-size: 30px;
  }
  .card-back .brand-square { width: 30px; height: 30px; }
  .rule {
    position: absolute; left: 190px; right: 0; top: 178px;
    height: 1.5px; background: var(--navy);
  }
  .edge-mark {
    position: absolute; left: 0; top: 184px; width: 16px; height: 34px;
    background: var(--navy);
  }
  .person { position: absolute; left: 38px; top: 132px; }
  .person-name {
    color: var(--navy); font-size: 25px; font-weight: 700;
    text-transform: uppercase; letter-spacing: -0.3px; line-height: 1;
  }
  .person-role {
    color: var(--teal); font-size: 12.5px; font-weight: 700;
    text-transform: uppercase; letter-spacing: 0.5px; margin-top: 4px;
  }
  .address {
    position: absolute; left: 58px; top: 200px;
    color: var(--teal); font-size: 15px; line-height: 21px;
  }
  .contacts {
    position: absolute; left: 40px; top: 258px; list-style: none;
    color: var(--teal); font-size: 15px; line-height: 22px;
  }
  .contacts li { display: flex; align-items: center; gap: 8px; }
  .contacts svg { width: 11px; height: 11px; flex: none; }
  .web-domain { color: var(--navy); }
</style>
</head>
<body>
  <section class="card card-front" aria-label="Card front">
    <div class="brand"><span class="brand-square"></span>Brightway Haus Inc.</div>
    <p class="tagline">Where Shine Counts</p>
  </section>

  <section class="card card-back" aria-label="Card back">
    <div class="brand"><span class="brand-square"></span>Brightway Haus Inc.</div>
    <div class="rule"></div>
    <div class="edge-mark"></div>
    <div class="person">
      <p class="person-name">Marlo Quinn</p>
      <p class="person-role">Director</p>
    </div>
    <p class="address">4180 Harbour Lane Suite<br>210 Oakridge ON K4R 2M6.</p>
    <ul class="contacts">
      <li>
        <svg viewBox="0 0 12 12" aria-hidden="true"><path d="M2.5 1l2 2.2-1 1.3c.7 1.5 1.9 2.7 3.4 3.4l1.3-1 2.3 2-1 1.6C5 10.5 1.5 7 .9 2z" fill="var(--navy)"/></svg>
        555-014-2290
      </li>
      <li>
        <svg viewBox="0 0 12 12" aria-hidden="true"><rect x="1" y="2.5" width="10" height="7" fill="none" stroke="var(--navy)" stroke-width="1.3"/><path d="M1 2.5l5 4 5-4" fill="none" stroke="var(--navy)" stroke-width="1.3"/></svg>
        info@brightwayhaus.ca
      </li>
      <li>
        <svg viewBox="0 0 12 12" aria-hidden="true"><circle cx="6" cy="6" r="4.8" fill="none" stroke="var(--navy)" stroke-width="1.2"/><path d="M1.2 6h9.6M6 1.2c-2.4 2.8-2.4 6.8 0 9.6M6 1.2c2.4 2.8 2.4 6.8 0 9.6" fill="none" stroke="var(--navy)" stroke-width="1"/></svg>
        <span>www.<span class="web-domain">thebrightwayhaus</span>.ca</span>
      </li>
    </ul>
  </section>
</body>
</html>
```